PROPERTY MANAGEMENT AND REAL ESTATE

Target Market(s)

real estate owners and investors

Industry/Entity Type

Real Estate

Contact Information for Business Card

BRIGHT LANTERN PROPERTY MANAGEMENT GROUP, LLC
287 North Willowmere Parkway
Suite 240
Hallandale Beach, FL 33071

```html
<!DOCTYPE html>
<html lang="en">
<head>
<meta charset="utf-8">
<title>Bright Lantern Property Management Group, LLC — Business Card</title>
<link href="https://fonts.googleapis.com/css2?family=Quicksand:wght@400;500&family=Roboto:wght@400;700&display=swap" rel="stylesheet">
<style>
  :root {
    --brand-red: #9c0e10;
    --deep-red: #7d0a0c;
    --ink: #1a1a1a;
    --paper: #ffffff;
    --mist-light: #f6f6f6;
    --mist-dark: #d9d9d9;
    --rule: #3a3a3a;
    --backdrop: #e9e7e4;
  }
  * { box-sizing: border-box; margin: 0; padding: 0; }
  html, body { width: 1200px; height: 790px; overflow: hidden; }
  body {
    background: var(--backdrop);
    font-family: "Quicksand", sans-serif;
    position: relative;
  }
  .card {
    position: absolute;
    top: 235px;
    width: 560px;
    height: 320px;
    overflow: hidden;
    box-shadow: 0 6px 18px rgba(0,0,0,.18);
  }
  .card--front { left: 27px; background: var(--paper); }
  .card--back { left: 613px; background: var(--brand-red); }

  .brand {
    display: flex;
    align-items: center;
    gap: 12px;
  }
  .brand__mark {
    width: 40px; height: 40px;
    background: var(--deep-red);
    flex: none;
  }
  .brand__name {
    color: var(--deep-red);
    font-weight: 400;
    font-size: 15px;
    line-height: 1.15;
    letter-spacing: .2px;
    text-transform: uppercase;
  }
  .card--front .brand {
    position: absolute;
    left: 50%; top: 50%;
    transform: translate(-50%, -50%);
  }

  .back__topband { position: absolute; left: 0; top: 0; width: 100%; height: 14px; background: var(--brand-red); }
  .back__header {
    position: absolute; left: 0; top: 14px; width: 100%; height: 124px;
    background: linear-gradient(180deg, var(--mist-light), var(--mist-dark));
  }
  .back__rule { position: absolute; left: 0; top: 138px; width: 100%; height: 4px; background: var(--rule); }
  .card--back .brand { position: absolute; left: 150px; top: 48px; }
  .card--back .brand__name { font-size: 13px; }
  .card--back .brand__mark { width: 34px; height: 34px; }

  .contacts { position: absolute; left: 300px; top: 92px; width: 260px; list-style: none; }
  .contact {
    position: relative;
    display: flex; align-items: center; gap: 9px;
    height: 20px; margin-bottom: 6px;
    padding-left: 8px;
    background: var(--paper);
    clip-path: polygon(4% 0, 100% 0, 100% 100%, 0 100%);
    font-family: "Roboto", sans-serif;
    font-size: 9.5px;
    color: var(--ink);
  }
  .contact--address { height: 40px; line-height: 1.3; }
  .contact__icon {
    width: 16px; height: 16px; flex: none;
    background: var(--ink);
    display: flex; align-items: center; justify-content: center;
  }
  .contact--address .contact__icon { height: 32px; }
  .contact__icon svg { width: 10px; height: 10px; }

  .person {
    position: absolute; left: 72px; top: 214px;
    width: 196px; height: 36px;
    background: linear-gradient(90deg, var(--paper), var(--mist-light));
    padding: 5px 0 0 14px;
    font-family: "Roboto", sans-serif;
  }
  .person::before {
    content: ""; position: absolute; left: -12px; top: 0;
    width: 12px; height: 100%; background: var(--ink);
  }
  .person__name { color: var(--brand-red); font-size: 11.5px; font-weight: 700; letter-spacing: .6px; }
  .person__title { color: var(--ink); font-size: 8.5px; letter-spacing: .4px; margin-top: 2px; }
</style>
</head>
<body>

<section class="card card--front" aria-label="Business card front">
  <div class="brand">
    <span class="brand__mark"></span>
    <p class="brand__name">Bright Lantern Property<br>Management Group, LLC</p>
  </div>
</section>

<section class="card card--back" aria-label="Business card back">
  <div class="back__topband"></div>
  <div class="back__header"></div>
  <div class="back__rule"></div>

  <div class="brand">
    <span class="brand__mark"></span>
    <p class="brand__name">Bright Lantern Property<br>Management Group, LLC</p>
  </div>

  <ul class="contacts">
    <li class="contact">
      <span class="contact__icon"><svg viewBox="0 0 10 10"><path d="M2 1 L4 1 L4.5 3 L3.3 4 Q4.3 6 6 6.7 L7 5.5 L9 6 L9 8 Q5 9 1.5 4.5 Q1 2.5 2 1Z" fill="#fff"/></svg></span>
      954 555 0142
    </li>
    <li class="contact">
      <span class="contact__icon"><svg viewBox="0 0 10 10"><rect x="3" y="1" width="4" height="8" rx=".6" fill="none" stroke="#fff" stroke-width="1"/><circle cx="5" cy="7.6" r=".5" fill="#fff"/></svg></span>
      954 555 0187
    </li>
    <li class="contact">
      <span class="contact__icon"><svg viewBox="0 0 10 10"><rect x="1" y="2.5" width="8" height="5.5" fill="none" stroke="#fff" stroke-width="1"/><path d="M1 2.5 L5 5.5 L9 2.5" fill="none" stroke="#fff" stroke-width="1"/></svg></span>
      dwhitcombe@brightlantern.com
    </li>
    <li class="contact">
      <span class="contact__icon"><svg viewBox="0 0 10 10"><circle cx="5" cy="5" r="3.8" fill="none" stroke="#fff" stroke-width="1"/><path d="M1.2 5 H8.8 M5 1.2 Q2.8 5 5 8.8 M5 1.2 Q7.2 5 5 8.8" fill="none" stroke="#fff" stroke-width=".8"/></svg></span>
      www.brightlanternpm.com
    </li>
    <li class="contact contact--address">
      <span class="contact__icon"><svg viewBox="0 0 10 10"><path d="M5 9.5 Q1.5 5.5 1.5 3.8 A3.5 3.5 0 0 1 8.5 3.8 Q8.5 5.5 5 9.5Z" fill="#c0161a"/><circle cx="5" cy="3.8" r="1.2" fill="#1a1a1a"/></svg></span>
      <span>287 North Willowmere Parkway, Suite 240<br>Hallandale Beach, FL 33071</span>
    </li>
  </ul>

  <div class="person">
    <p class="person__name">DANIEL WHITCOMBE</p>
    <p class="person__title">FINANCIAL ADVISOR</p>
  </div>
</section>

</body>
</html>
```